Upmarket Dessert Lounge needs a Business Card Design

We are an upmarket dessert lounge needing a business card to match our image.

We want something that is simple yet beautiful, feminine, classy, sophisticated and elegant. We want it to stand out and don't mind if it is bold.

The design should include our logo and colours of red or maroon with gold highlights. We don't mind if black is used.

Marlow & Quince

Target Market(s)

For those who like to indulge or treat themselves and give in to their temptations on good quality desserts.

Industry/Entity Type

Business

Requirements
Must have
• Must include our logo and our name

Marlow & Quince

M & Q

```html
<!DOCTYPE html>
<html lang="en">
<head>
<meta charset="utf-8">
<title>Marlow &amp; Quince – Business Card</title>
<link rel="stylesheet" href="https://fonts.googleapis.com/css2?family=PT+Sans:wght@400;700&display=swap">
<style>
  :root {
    --backdrop: #dcdcdc;
    --card-white: #ffffff;
    --peach: #fdd39a;
    --maroon: #7a1315;
    --ink: #1a1a1a;
    --text-font: "PT Sans", "Myriad Pro", Arial, sans-serif;
  }
  * { margin: 0; padding: 0; box-sizing: border-box; }
  html, body {
    width: 956px;
    height: 1200px;
    overflow: hidden;
    background: var(--backdrop);
    font-family: var(--text-font);
    color: var(--ink);
  }
  .canvas { position: relative; width: 956px; height: 1200px; }

  .card {
    position: absolute;
    border-radius: 28px;
    overflow: hidden;
  }
  .card-front {
    left: 80px; top: 118px;
    width: 796px; height: 455px;
    background: var(--card-white);
  }
  .card-back {
    left: 75px; top: 635px;
    width: 797px; height: 453px;
    background: var(--peach);
  }
  .front-shapes { position: absolute; inset: 0; }
  .front-shapes .peach-panel { fill: var(--peach); }
  .front-shapes .maroon-swoosh { fill: var(--maroon); }

  .brand-name {
    position: absolute;
    color: var(--maroon);
    font-weight: 400;
    white-space: nowrap;
    transform: translate(-50%, -50%);
    letter-spacing: 2px;
  }
  .card-front .brand-name { left: 190px; top: 190px; font-size: 84px; }
  .card-back .brand-name { left: 396px; top: 228px; font-size: 120px; }

  .contact-block {
    position: absolute;
    left: 530px;
    transform: translateX(-50%);
    text-align: center;
    white-space: nowrap;
  }
  .person { top: 82px; }
  .person-name { font-size: 25px; font-weight: 700; line-height: 1.1; }
  .person-role { font-size: 19px; line-height: 1.3; }

  .numbers { top: 217px; font-size: 19px; line-height: 36px; }
  .online { top: 365px; font-size: 19px; line-height: 33px; }
  .label { font-weight: 700; }

  .address {
    position: absolute;
    left: 185px; top: 365px;
    transform: translateX(-50%);
    text-align: center;
    font-size: 19px;
    line-height: 27px;
    white-space: nowrap;
  }
</style>
</head>
<body>
<main class="canvas">
  <section class="card card-front" aria-label="Business card front">
    <svg class="front-shapes" width="796" height="455" viewBox="0 0 796 455" aria-hidden="true">
      <path class="peach-panel" d="M412 0 C372 60 368 150 388 250 C403 330 412 400 402 455 L796 455 L796 0 Z"/>
      <path class="maroon-swoosh" d="M371 92 C394 200 420 330 380 455 L396 455 C430 330 402 190 371 92 Z"/>
    </svg>

    <div class="brand-name">M &amp; Q</div>

    <div class="contact-block person">
      <p class="person-name">Your Name</p>
      <p class="person-role">Designation</p>
    </div>
    <div class="contact-block numbers">
      <p><span class="label">p</span> : 123-456-7890</p>
      <p><span class="label">c</span> : 123-456-7890</p>
      <p><span class="label">f</span> : 123-456-7890</p>
    </div>
    <div class="contact-block online">
      <p><span class="label">e</span> : name@yourwebsite.com</p>
      <p><span class="label">w</span> : www.marlow&amp;quince.com</p>
    </div>

    <div class="address">
      <p>0000, Street Name</p>
      <p>City Name, Country Code.</p>
    </div>
  </section>

  <section class="card card-back" aria-label="Business card back">
    <div class="brand-name">M &amp; Q</div>
  </section>
</main>
</body>
</html>
```